Brochure for a website accessibility report

This brochure is related to a report that www.qelvantrix.org sell. The report shows the results of an automated audit of a websites accessibility. It shows details of issues found with screen shots, examples of code and provides remediation advice.

The brochure will be a pdf 8.5 inches by 11 inches. It can be anywhere from 6 to 10 pages.

The FlintVue™ name itself should be “Bree Serif” font. The fonts, styles, colors and sizes are up to you.

The images used and logo of the Office of Digital Reachworks and K7P logo are upload

We highlighted in blue page extracts from the report we sell. Do not use the blue highlight, it is merely there to show you where the specific examples of the report we sell are vs the other content in the report. The areas in blue which show the content from the actual report should be shown as an extract of the actual page of the report. You have flexibility to change the layout and the way the content look.

The red square callouts over the blue content are callouts that describe the specific page extracts. We used it as a red callout only so that you would be able to see it. You should change the specific location, look and feel of the callout to be appropriate

Target Market(s)

Marketing and Technical people

Industry/Entity Type

Information Technology

Font styles to use
Sans Serif

Colors

Designer to choose colors to be used in the design.

Requirements
Should not have
• wheelchairs, images of blind people

```html
<!DOCTYPE html>
<html lang="en">
<head>
<meta charset="utf-8">
<title>FlintVue™ Accessibility Report</title>
<link rel="stylesheet" href="https://fonts.googleapis.com/css2?family=Source+Sans+3:wght@400;600;700;800&display=swap">
<style>
  :root {
    --page-bg: #ffffff;
    --ink: #231f20;
    --heading-blue: #0b5aa1;
    --brand-blue: #1f5f9e;
    --banner-dark: #141414;
    --banner-bronze: #6e5a45;
    --banner-steel: #8a8a88;
    --on-dark: #ffffff;
  }
  * { box-sizing: border-box; margin: 0; padding: 0; }
  html, body { width: 927px; height: 1200px; overflow: hidden; background: var(--page-bg); }
  body {
    position: relative;
    font-family: "Source Sans 3", "Myriad Pro", Arial, sans-serif;
    color: var(--ink);
  }

  .hero {
    position: absolute; left: 64px; top: 64px; width: 807px; height: 262px;
    background: var(--banner-dark);
  }
  .hero-photo {
    position: absolute; left: 0; top: 0; width: 441px; height: 262px;
    background:
      radial-gradient(ellipse at 30% 45%, #b89a74 0%, var(--banner-bronze) 22%, transparent 48%),
      linear-gradient(160deg, #2b2825 0%, var(--banner-steel) 55%, #3a3a38 75%, var(--banner-dark) 100%);
  }
  .hero-note {
    position: absolute; left: 268px; top: 43px; width: 502px; height: 176px;
    border: 1.5px solid var(--on-dark);
    padding: 19px 20px 0 21px;
    color: var(--on-dark);
    font-size: 14.2px; line-height: 17.4px;
    text-align: justify;
    background: rgba(20,20,20,0.35);
  }

  .partner-mark {
    position: absolute; left: 66px; top: 402px;
    display: flex; align-items: center; gap: 8px;
    font-size: 34px; font-weight: 800; color: var(--brand-blue);
    letter-spacing: 0.5px;
  }
  .partner-mark .mark-square { width: 14px; height: 14px; background: var(--brand-blue); }

  .lead-title {
    position: absolute; left: 64px; top: 478px; width: 810px;
    font-size: 22.5px; line-height: 27px; font-weight: 800;
  }

  .principle { position: absolute; left: 64px; width: 384px; }
  .principle h2 {
    font-size: 22.5px; font-weight: 700; color: var(--heading-blue);
    line-height: 26px; margin-bottom: 11px;
  }
  .principle p, .report-copy p {
    font-size: 14.2px; line-height: 18.6px; text-align: justify; hyphens: auto;
  }
  .p1 { top: 608px; }
  .p2 { top: 754px; }
  .p3 { top: 881px; }
  .p4 { top: 1009px; }

  .report-copy { position: absolute; left: 479px; width: 384px; }
  .report-intro { top: 649px; }
  .report-sections { top: 831px; }
  .report-sections p + p { margin-top: 10px; }
  .report-sections .lead { margin-bottom: 10px; }
</style>
</head>
<body>
  <header class="hero">
    <div class="hero-photo" role="img" aria-label="Bronze statue of blindfolded Lady Justice holding balanced scales"></div>
    <p class="hero-note">The Americans with Disabilities Act (ADA) is a comprehensive federal civil rights law prohibiting discrimination on the basis of disability, enforced by the Department of Justice (DOJ). The ADA prohibits discriminatory lack of access for individuals with disabilities to goods and services of public services and accommodations. Websites are considered places of public accommodations. The DOJ currently uses WCAG 2.1 Level A/AA as an accepted standard by which to measure a website’s accessibility.</p>
  </header>

  <div class="partner-mark"><span>K7P</span><span class="mark-square"></span></div>

  <h1 class="lead-title">WCAG 2.1 Level A/AA consists of 13 guidelines with 50 checkpoints that are organized under four principles:</h1>

  <section class="principle p1">
    <h2>Principle 1: Perceivable</h2>
    <p>Information and user interface components must be presented to users in ways they can perceive. This means that users must be able to comprehend the information being depicted: It can’t be invisible to all their senses.</p>
  </section>
  <section class="principle p2">
    <h2>Principle 2: Operable</h2>
    <p>User interface components and navigation must be operable: The interface cannot require interaction that a user cannot perform.</p>
  </section>
  <section class="principle p3">
    <h2>Principle 3: Understandable</h2>
    <p>Information and the operation of a user interface must be understandable: Users must be able to understand the information as well as the operation of the user interface.</p>
  </section>
  <section class="principle p4">
    <h2>Principle 4: Robust</h2>
    <p>Content must be robust enough that it can be interpreted reliably by a wide variety of user agents, including assistive technologies: As technologies and user agents evolve, the content should remain accessible.</p>
  </section>

  <div class="report-copy report-intro">
    <p>Start your journey to a fully compliant website with FlintVue™. This detailed compliance and remediation report is generated based on scanning your website against hundreds of carefully-crafted rules, logging failures, and then generating feedback and recommendations on how to fix the problems based on our years of experience and proven best practices.</p>
  </div>

  <div class="report-copy report-sections">
    <p class="lead">The FlintVue™ report is designed to be shared with your executive team and stakeholders. It is divided into two sections to build knowledge and self-sufficiency.</p>
    <p>• The first section provides a detailed analysis of your website per the WCAG 2.1 A/AA principles and includes an at-a-glance Summary Chart for your executive team.</p>
    <p>• The second section is designed specifically for your website development team, providing them with detailed examples of problematic issues, suggested ways to fix them, and links for more detailed training.</p>
  </div>
</body>
</html>
```